Maple Bus Card

i own a building in the bronx ny - its called "Maple Larkwell Residences"i want a classy logo / business card - nothing too religuous but it is like a family there - its a large apartment building - colors i like dark red, black, medium shade of gray also reg business card stuff tel # 914-555-0173 address 4738 Larkwell Ave Bronx NY 10460 Email fijosh@aol.comslogan - " One roof, one family "i can send u a picture of the building for the backside

```html
<!DOCTYPE html>
<html lang="en">
<head>
<meta charset="utf-8">
<title>Maple Larkwell Residences – Business Card</title>
<link rel="stylesheet" href="https://fonts.googleapis.com/css2?family=Source+Sans+3:wght@400;600;700&display=swap">
<style>
  :root {
    --page-bg: #e6e6e6;
    --card-white: #ffffff;
    --brand-red: #c8202c;
    --brand-red-deep: #9a1118;
    --brand-red-bright: #d6232e;
    --ink: #1f1f1f;
    --ink-soft: #3a3a3a;
    --gold: #e2b65a;
    --gold-soft: #f2d48a;
  }
  * { margin: 0; padding: 0; box-sizing: border-box; }
  html, body {
    width: 1200px;
    height: 800px;
    overflow: hidden;
    background: var(--page-bg);
    font-family: "Source Sans 3", "Myriad Pro", Arial, sans-serif;
  }
  .canvas {
    width: 1200px;
    height: 800px;
    display: flex;
    align-items: center;
    justify-content: center;
    gap: 40px;
  }
  .card {
    position: relative;
    width: 540px;
    height: 309px;
    border-radius: 4px;
    overflow: hidden;
    box-shadow: 0 2px 8px rgba(0,0,0,0.12);
  }

  /* Back side */
  .card--back {
    background: radial-gradient(ellipse at 58% 55%, var(--brand-red-bright) 0%, var(--brand-red) 40%, var(--brand-red-deep) 100%);
  }
  .back-brand {
    position: absolute;
    top: 62px;
    left: 0;
    right: 0;
    text-align: center;
  }
  .back-name {
    color: var(--gold);
    font-weight: 700;
    font-size: 24px;
    line-height: 1.1;
    letter-spacing: 0.3px;
    text-transform: uppercase;
  }
  .back-slogan {
    margin-top: 4px;
    color: var(--gold-soft);
    font-size: 12px;
    letter-spacing: 0.6px;
    text-transform: uppercase;
  }

  /* Front side */
  .card--front { background: var(--card-white); }
  .brand {
    position: absolute;
    top: 62px;
    right: 34px;
    text-align: right;
  }
  .brand-name {
    color: var(--ink);
    font-weight: 700;
    font-size: 20px;
    line-height: 1.1;
    text-transform: uppercase;
  }
  .brand-slogan {
    margin-top: 3px;
    color: var(--brand-red);
    font-size: 11.5px;
    text-transform: uppercase;
  }
  .identity {
    position: absolute;
    left: 34px;
    top: 148px;
  }
  .identity-tab {
    position: absolute;
    left: 0;
    top: 164px;
    width: 6px;
    height: 38px;
    background: var(--brand-red);
    border-radius: 0 2px 2px 0;
  }
  .person-name {
    color: var(--ink);
    font-weight: 700;
    font-size: 24px;
    line-height: 1;
  }
  .person-role {
    margin-left: 10px;
    color: var(--brand-red);
    font-size: 17px;
    line-height: 1.3;
  }
  .contact-list {
    list-style: none;
    margin-top: 8px;
    margin-left: 18px;
  }
  .contact-item {
    display: flex;
    align-items: center;
    gap: 12px;
    color: var(--ink-soft);
    font-size: 18px;
    line-height: 26px;
  }
  .contact-icon { width: 14px; height: 14px; flex: none; }
  .bottom-band {
    position: absolute;
    left: 0;
    right: 0;
    bottom: 0;
    height: 8px;
    background: var(--brand-red);
  }
  .bottom-band::before {
    content: "";
    position: absolute;
    left: 0;
    right: 0;
    top: -4px;
    height: 2px;
    background: var(--brand-red);
  }
</style>
</head>
<body>
  <main class="canvas">
    <section class="card card--back" aria-label="Card back">
      <div class="back-brand">
        <div class="back-name">Maple Larkwell Residences</div>
        <div class="back-slogan">One roof, one family</div>
      </div>
    </section>

    <section class="card card--front" aria-label="Card front">
      <div class="brand">
        <div class="brand-name">Maple Larkwell Residences</div>
        <div class="brand-slogan">One roof, one family</div>
      </div>

      <span class="identity-tab"></span>
      <div class="identity">
        <div class="person-name">YOUR NAME</div>
        <div class="person-role">POSITION</div>
        <ul class="contact-list">
          <li class="contact-item">
            <svg class="contact-icon" viewBox="0 0 24 24" aria-hidden="true">
              <path fill="#c8202c" d="M6.6 10.8a15.1 15.1 0 0 0 6.6 6.6l2.2-2.2a1 1 0 0 1 1-.25 11.4 11.4 0 0 0 3.6.57 1 1 0 0 1 1 1V20a1 1 0 0 1-1 1A17 17 0 0 1 3 4a1 1 0 0 1 1-1h3.5a1 1 0 0 1 1 1c0 1.25.2 2.45.57 3.57a1 1 0 0 1-.25 1z"/>
            </svg>
            914-555-0173
          </li>
          <li class="contact-item">
            <svg class="contact-icon" viewBox="0 0 24 24" aria-hidden="true">
              <rect x="2" y="5" width="20" height="14" fill="none" stroke="#c8202c" stroke-width="2"/>
              <path d="M2 5l10 8 10-8M2 19l7-7M22 19l-7-7" fill="none" stroke="#c8202c" stroke-width="2"/>
            </svg>
            mavreld@quintmail.com
          </li>
          <li class="contact-item">
            <svg class="contact-icon" viewBox="0 0 24 24" aria-hidden="true">
              <path fill="#c8202c" d="M12 2a7 7 0 0 0-7 7c0 5.2 7 13 7 13s7-7.8 7-13a7 7 0 0 0-7-7zm0 9.5A2.5 2.5 0 1 1 12 6.5a2.5 2.5 0 0 1 0 5z"/>
            </svg>
            4738 Larkwell Ave, Bronx NY 10460
          </li>
        </ul>
      </div>

      <div class="bottom-band"></div>
    </section>
  </main>
</body>
</html>
```